Business Card Design for Varomir Facility Services

We are looking for a Business Card Design for the Company "Varomir Facility Services."
Front side:
- Company Logo (small)
- Company Name, address, pohone, website and personal data.
- white background, for text e.g. company colors (blue or green like in the logo)
Please use following data:
Company data:
Varomir Facility Services Kostelac
Birkenhaldweg 14
6319 Seewil
www.varomir-fs.ch
Person data:
Tarik Kostelac
Geschäftsführer
+41 76 519 47 83
info@varomir-fs.ch
Back side:
could be colored in blue or green
please use a big logo sing and some smaller icons to say what is all beeing offered in facility services, like cleaning, maintenance cleaning
industrial cleaning, caretaking, gardening, disposal. There is no need for everyone of the icons if there are similar or an icon is standing for more of them.
colors to use:
blue: HEX 246BB0
green: HEX 52B33E

```html
<!DOCTYPE html>
<html lang="de">
<head>
<meta charset="utf-8">
<title>Varomir Facility Services – Business Card</title>
<link rel="stylesheet" href="https://fonts.googleapis.com/css2?family=Lato:wght@400;700&display=swap">
<style>
  :root {
    --blue: #246BB0;
    --green: #52B33E;
    --ink: #1e1e1e;
    --paper: #ffffff;
    --backdrop: #d9d9d9;
  }
  * { margin: 0; padding: 0; box-sizing: border-box; }
  html, body { width: 1200px; height: 802px; overflow: hidden; }
  body {
    background: var(--backdrop);
    font-family: "Lato", sans-serif;
    position: relative;
  }
  .card {
    position: absolute;
    top: 274px;
    width: 443px;
    height: 265px;
    box-shadow: 0 3px 8px rgba(0,0,0,0.35);
    overflow: hidden;
  }
  /* Front */
  .card--front { left: 136px; background: var(--paper); }
  .front__stripe-blue {
    position: absolute; left: 0; top: 0; bottom: 0; width: 38px;
    background: var(--blue);
  }
  .front__stripe-green {
    position: absolute; left: 38px; top: 0; bottom: 0; width: 4px;
    background: var(--green);
  }
  .brand {
    position: absolute;
    display: flex; align-items: center; gap: 8px;
    color: var(--blue);
    font-weight: 700;
    white-space: nowrap;
  }
  .brand__dot { border-radius: 50%; background: var(--green); flex: none; }
  .front__brand { right: 26px; top: 40px; font-size: 17px; letter-spacing: 0.5px; }
  .front__brand .brand__dot { width: 14px; height: 14px; }
  .person { position: absolute; left: 60px; top: 106px; }
  .person__name {
    color: var(--blue); font-weight: 700; font-size: 16.5px;
    text-transform: uppercase; letter-spacing: 0.3px; line-height: 1.15;
  }
  .person__role { color: var(--ink); font-size: 12.5px; line-height: 1.2; }
  .contact { list-style: none; margin-top: 7px; }
  .contact__item {
    display: flex; align-items: center; gap: 5px;
    color: var(--ink); font-size: 12.5px; line-height: 16px;
  }
  .contact__icon { width: 10px; height: 10px; flex: none; fill: var(--blue); }
  .company { margin-top: 6px; font-size: 12.5px; line-height: 16px; color: var(--ink); }
  .company__name { color: var(--green); }
  /* Back */
  .card--back { left: 624px; background: var(--blue); }
  .back__brand {
    left: 0; right: 0; top: 100px; justify-content: center;
    color: var(--paper); font-size: 26px; letter-spacing: 1.5px;
  }
  .back__brand .brand__dot { width: 20px; height: 20px; background: var(--paper); }
  .services {
    position: absolute; left: 0; right: 0; top: 182px; height: 45px;
    background: var(--green);
    display: flex; flex-direction: column; justify-content: center; align-items: center;
    color: var(--paper); font-size: 11px; font-weight: 400; line-height: 14px; text-transform: uppercase;
    letter-spacing: 0.2px;
  }
</style>
</head>
<body>
  <section class="card card--front" aria-label="Card front">
    <div class="front__stripe-blue"></div>
    <div class="front__stripe-green"></div>
    <div class="brand front__brand"><span class="brand__dot"></span>Varomir Facility Services</div>
    <div class="person">
      <p class="person__name">Tarik Kostelac</p>
      <p class="person__role">Geschäftsführer</p>
      <ul class="contact">
        <li class="contact__item">
          <svg class="contact__icon" viewBox="0 0 10 10"><path d="M1 3 Q5 0 9 3 L8 4.5 L6.5 3.8 V3 H3.5 V3.8 L2 4.5 Z M2.5 5 H7.5 L8.5 9 H1.5 Z"/></svg>
          +41 76 519 47 83
        </li>
        <li class="contact__item">
          <svg class="contact__icon" viewBox="0 0 10 10"><path d="M0.5 2 H9.5 V8 H0.5 Z M1 2.5 L5 5.5 L9 2.5" stroke="#fff" stroke-width="0.8"/></svg>
          info@varomir-fs.ch
        </li>
        <li class="contact__item">
          <svg class="contact__icon" viewBox="0 0 10 10"><circle cx="5" cy="5" r="4.5"/></svg>
          www.varomir-fs.ch
        </li>
      </ul>
      <div class="company">
        <p class="company__name">Varomir Facility Services Kostelac</p>
        <p>Birkenhaldweg 14</p>
        <p>6319 Seewil</p>
      </div>
    </div>
  </section>

  <section class="card card--back" aria-label="Card back">
    <div class="brand back__brand"><span class="brand__dot"></span>Varomir Facility Services</div>
    <div class="services">
      <p>Cleaning | Maintenance Cleaning | Industrial Cleaning</p>
      <p>Caretaking | Gardening | Disposal</p>
    </div>
  </section>
</body>
</html>
```